Website to design and sell sundials: www.gnomonvale.com

We have a website that creates a free paper sundial, we want to migrate from this not profit free website to a website where we will continue offering the free paper sundial model but We will also offer a manufactured sundial and sell it.
In order to understand the project, please visit:
http://www.gnomonvale.com/vertical/sundial.html and
http://www.torvel.net/landing/

The website user journey should be redesigned, including the phases that are,
select language
Show product give info
Creation/edit sundial (could be one or more phases)
View created sundial
Buy sundial.

May some of them could be combined or splitted, what It have more sense.

Requirements
Must have
• A description page user journey offering freemium paper sundial and physical sundial to sell.
• A sundial creation page for "free" paper sundial
• A result page for paper sundial
• A sell page for physical

```html
<!DOCTYPE html>
<html lang="en">
<head>
<meta charset="utf-8">
<title>GnomonVale – How to make a paper sundial</title>
<link href="https://fonts.googleapis.com/css2?family=Roboto:wght@300;400;500;700&display=swap" rel="stylesheet">
<style>
:root{
  --red:#c0332f;
  --red-dark:#a7241f;
  --orange:#f7ac3b;
  --orange-light:#fbc04a;
  --orange-deep:#eb9b1c;
  --dark:#2b2b2b;
  --black:#1d1d1d;
  --grey-bg:#f2f2f2;
  --text:#333;
  --muted:#7b7b7b;
  --white:#fff;
}
*{box-sizing:border-box;margin:0;padding:0}
html,body{width:1200px;height:2203px;overflow:hidden}
body{font-family:'Roboto',Arial,sans-serif;color:var(--text);background:var(--white);position:relative}
a{color:inherit;text-decoration:none}
.top-strip{height:7px;background:var(--red)}
.header{height:113px;position:relative}
.brand{position:absolute;left:100px;top:47px;display:flex;align-items:center;gap:10px;font-size:26px;font-weight:500;color:var(--red)}
.brand-dot{width:22px;height:22px;border-radius:50%;background:var(--red)}
.header-phone{position:absolute;left:775px;top:44px;font-size:21px;color:#666;display:flex;align-items:center;gap:14px;font-weight:300}
.lang{position:absolute;left:977px;top:37px;width:134px;height:43px;border:2px solid #555;display:flex;align-items:center;justify-content:center;gap:8px;font-size:16px;color:#333}
.nav{height:75px;background:linear-gradient(var(--orange-light),var(--orange-deep));position:relative}
.nav a{position:absolute;top:0;height:75px;line-height:75px;color:var(--white);font-size:16px}
.nav .active{left:85px;width:113px;background:var(--red);text-align:center}
.title-band{height:113px;background:var(--dark);color:var(--white);text-align:center;line-height:113px;font-size:30px;font-weight:400}
.intro h2{position:absolute;top:350px;left:0;width:1200px;text-align:center;font-size:27px;font-weight:400;color:#222}
.intro p{position:absolute;top:393px;left:91px;width:1018px;text-align:center;font-size:12.5px;line-height:23px;color:var(--muted)}
.photo{position:absolute;border:5px solid var(--white);box-shadow:0 0 5px rgba(0,0,0,.35)}
.caption{position:absolute;top:770px;width:500px;font-size:12.5px;line-height:23px;color:#333}
.need{position:absolute;top:928px;left:0;width:1200px;height:387px;background:var(--grey-bg)}
.need h3{position:absolute;left:554px;top:47px;font-size:20px;font-weight:400;color:var(--red)}
.need-body{position:absolute;left:554px;top:85px;font-size:14px;color:#555;line-height:28px}
.need-body .tools span{margin-right:32px}
.need-body ul{list-style:none}
.need-body li:before{content:"» ";color:var(--red)}
.instructions{position:absolute;top:1318px;left:0;width:1200px;height:396px;background:var(--orange)}
.instructions h3{position:absolute;left:87px;top:60px;font-size:21px;font-weight:400;color:var(--white)}
.steps{position:absolute;left:87px;top:96px;width:570px;font-size:13.5px;line-height:28px;color:var(--white);font-weight:300}
.steps .cta{color:var(--red-dark);font-size:18px;font-weight:500}
.steps .small{font-size:12.5px;line-height:22px}
.steps .buy{color:var(--red-dark);font-weight:500;font-size:14px}
.samples h3{position:absolute;top:1782px;left:0;width:1200px;text-align:center;font-size:20px;font-weight:400;color:var(--red)}
.samples ul{position:absolute;top:1842px;left:135px;list-style:none;display:flex;font-size:17px;color:#333}
.samples li:before{content:"» ";color:var(--red);font-size:14px}
.footer{position:absolute;top:1920px;left:0;width:1200px;height:220px;background:var(--red);color:var(--white)}
.footer h4{position:absolute;top:36px;font-size:15px;font-weight:500}
.footer .col{position:absolute;top:75px;font-size:12px;line-height:17px}
.links li{list-style:none;line-height:24.5px}
.links li:before{content:"▸ ";font-size:9px}
.subscribe{display:flex;margin-top:14px}
.subscribe span{width:145px;height:31px;background:#f3f3f3;color:#999;font-size:11px;line-height:31px;padding-left:13px}
.subscribe b{width:56px;height:31px;background:var(--orange-deep);font-weight:400;font-size:11px;line-height:31px;text-align:center}
.socials{display:flex;gap:16px;margin-top:18px}
.socials i{width:33px;height:33px;border:1.5px solid var(--white);border-radius:50%}
.bottom{position:absolute;top:2140px;left:0;width:1200px;height:63px;background:var(--black);color:var(--white);font-size:11px;text-align:center;line-height:63px}
</style>
</head>
<body>
<div class="top-strip"></div>
<header class="header">
  <a class="brand" href="#"><span class="brand-dot"></span>GnomonVale.com</a>
  <div class="header-phone">
    <svg width="20" height="20" viewBox="0 0 24 24"><path fill="#c0332f" d="M6.6 10.8a15 15 0 0 0 6.6 6.6l2.2-2.2c.3-.3.7-.4 1-.2 1.1.4 2.3.6 3.6.6.6 0 1 .4 1 1V20c0 .6-.4 1-1 1A17 17 0 0 1 3 4c0-.6.4-1 1-1h3.5c.6 0 1 .4 1 1 0 1.3.2 2.5.6 3.6.1.3 0 .7-.2 1z"/></svg>
    (888)555-0147
  </div>
  <div class="lang">
    <svg width="30" height="19" viewBox="0 0 30 19"><rect width="30" height="19" fill="#b22234"/><g fill="#fff"><rect y="3" width="30" height="2"/><rect y="7.5" width="30" height="2"/><rect y="12" width="30" height="2"/><rect y="16.5" width="30" height="1.5"/></g><rect width="13" height="10" fill="#3c3b6e"/></svg>
    English
    <svg width="9" height="6" viewBox="0 0 9 6"><path d="M1 1l3.5 3.5L8 1" stroke="#333" fill="none" stroke-width="1.5"/></svg>
  </div>
</header>
<nav class="nav">
  <a class="active" href="#">HOME</a>
  <a href="#" style="left:221px">ABOUT US</a>
  <a href="#" style="left:355px">OUR SERVICES</a>
  <a href="#" style="left:523px">PRODUCTS</a>
  <a href="#" style="left:667px">BLOG</a>
  <a href="#" style="left:765px">NEWS</a>
  <a href="#" style="left:868px">LOCATION</a>
  <a href="#" style="left:1002px">CONTACT</a>
</nav>
<h1 class="title-band">HOW TO MAKE A PAPER SUNDIAL</h1>

<section class="intro">
  <h2>INTRODUCTION</h2>
  <p>This page is about Sundials. Sundials are instruments that tell you the time with the shadow of the sun. To design a sundial you need to know exactly where you are going to put it, i.e. you need to know the longitude, the latitude and the orientation of the wall with respect to North. I have designed this page and integrated OrbitMaps. It helps you to easily find all the parameters needed and finally produces a printable page with a cut-out paper sundial, that can be cut and folded to give you a vertical sundial.This page allows you to make your own Cut Out Paper Vertical Sundial customized to your place on earth and the declination of the wall you are going to put it on.</p>
</section>

<div class="photo" role="img" aria-label="Paper sundial fixed to a brick wall" style="left:85px;top:517px;width:498px;height:235px;background:linear-gradient(90deg,#3b3f2e 0%,#3b3f2e 20%,#a4604a 24%,#b0664d 100%)"></div>
<div class="photo" role="img" aria-label="Paper sundial fixed to a window" style="left:613px;top:517px;width:498px;height:235px;background:linear-gradient(90deg,#1a1a16 0%,#1a1a16 28%,#8aa0b8 36%,#d8c8b2 60%,#6c7c8c 100%)"></div>
<p class="caption" style="left:86px">Moreover, you have the possibility to put your vertical Sundial on a window and read the hour from inside the room. In this case the numbers are printed to be read from inside.</p>
<p class="caption" style="left:617px">Your sundial can be configured to show civil time or civil daylight-saving time, so that it gives you your country's official time as you can see it on TV or your watch. Further-more it can be configured to show the natural "true local time" as you can see it on</p>

<section class="need">
  <div class="photo" role="img" aria-label="Aerial satellite view of a building with a red line along one wall" style="left:90px;top:38px;width:429px;height:300px;background:linear-gradient(135deg,#4a4a40,#8e8c80 50%,#3e3e36)"></div>
  <h3>WHAT YOU NEED</h3>
  <div class="need-body">
    <div class="tools"><span>1. This webpage</span><span>2. A printer</span><span>3. Scissors</span></div>
    <div style="margin-top:8px">1. Where is the wall where you want to put your sundial on, located it with OrbitMaps.</div>
    <ul>
      <li>Zoom in as far as possible.</li>
      <li>Click once at one end of a long wall.</li>
      <li>Move to and click again on the other end.</li>
      <li>This draws a red line parallel to the wall, and defines the orientation.</li>
    </ul>
    <div style="margin-top:4px">2. Select the N/S/E/W face desired, from the pull-down menu.</div>
    <div>3. Select your timezone or true local time for solar time</div>
    <div>4. Select if you are Daylight saving time</div>
  </div>
</section>

<section class="instructions">
  <h3>INSTRUCTIONS</h3>
  <div class="steps">
    <div>1. CALCULATE.</div>
    <a class="cta" href="#">Click here to build your custom sundial!!!</a>
    <div class="small">Fill in the form and create your sundial</div>
    <div style="margin-top:6px">2. PRINT THE PDF. To print, please select "shrink to page" in order not to deform the shape of the page.</div>
    <div>3. CUT AND FOLD: Once you have your model printed, you have to cut (RED LINES), and fold (BLUE LINES)</div>
    <div>4. PUT ON YOUR WALL. Put on your wall or Window.</div>
    <div>5. ENJOY. <a class="buy" href="#">» Or order it manufactured in metal</a></div>
  </div>
  <div class="photo" role="img" aria-label="Printed sundial template with red cut lines and blue fold lines" style="left:676px;top:54px;width:429px;height:300px;background:radial-gradient(circle,#fafafa 45%,#d9d9d9)"></div>
</section>

<section class="samples">
  <h3>SUNDIAL SAMPLES</h3>
  <ul>
    <li style="width:320px">South Hemisphere Buenos Aires</li>
    <li style="width:224px">Valencia South east</li>
    <li style="width:247px">Valencia NORTH WEST</li>
    <li>Valencia WEST</li>
  </ul>
</section>

<footer class="footer">
  <h4 style="left:98px">LINKS</h4>
  <ul class="col links" style="left:98px;top:70px">
    <li>Customer Support</li><li>Documentation</li><li>Resources</li><li>General FAQs</li><li>Shortcodes</li>
  </ul>
  <h4 style="left:311px">NEQUE PORRO QUISQUAM</h4>
  <p class="col" style="left:311px;width:252px">Lorem Ipsum has been the industry's standard dummy text ever since the 1500s, when an unknown printer took a galley of type and scrambled it to make a type specimen book. It has survived not only five centuries, but also the leap into electronic typesetting, remaining</p>
  <h4 style="left:650px">GET IN TOUCH</h4>
  <div class="col" style="left:651px;width:220px;line-height:24px">
    <div>Address : 72 Meridian Lane, Kelvarn,<br>Ontario K4B1T8</div>
    <div style="margin-top:11px">Phone : 1 844 555-0193</div>
    <div style="margin-top:11px">Email : hello@gnomonvale.com</div>
  </div>
  <h4 style="left:908px">NEWSLETTER</h4>
  <div class="col" style="left:908px;width:210px">
    <div>Your about us information would fit here nicely.</div>
    <div class="subscribe"><span>Email address</span><b>Submit</b></div>
    <div class="socials"><i></i><i></i><i></i></div>
  </div>
</footer>
<div class="bottom">Copyright © 2016. All Rights Reserved</div>
</body>
</html>
```